Mastering Modern Vineyard Management

size of the ad - 8”x 10.75" plus 0.25" bleed
I would like an ad for a magazine that will stand out and make people want to read the ad.
The ad should not be crowded and people reading the ad will be able to read the text.
I would like it to be a creative and modern-day design.
the list of topics should not be the focus of the ad.
the text is attached.
If you decide to use people in the ad then please no ladies.
please note that leave over 1 inch for the bottom of the footer

```html
<!DOCTYPE html>
<html lang="en">
<head>
<meta charset="utf-8">
<title>Vineyard Course – Mastering Modern Vineyard Management</title>
<link rel="stylesheet" href="https://fonts.googleapis.com/css2?family=Montserrat:wght@300;400;800;900&family=Raleway:wght@300;700&family=Lato:wght@400;700&family=Red+Hat+Display:wght@700&display=swap">
<style>
  :root {
    --navy: #11466f;
    --navy-ink: #0f4571;
    --sky: #79c7ef;
    --slate: #42618f;
    --white: #ffffff;
    --paper: #ffffff;
    --icon-ink: #123f63;
    --ring-ink: #1b2a38;
    --rule: #8a99a8;
  }
  * { margin: 0; padding: 0; box-sizing: border-box; }
  html, body { width: 900px; height: 1200px; overflow: hidden; background: var(--paper); }
  .ad { position: relative; width: 900px; height: 1200px; overflow: hidden; background: var(--paper); }

  .hero-scene {
    position: absolute; left: 0; top: 0; width: 900px; height: 555px;
    background:
      radial-gradient(ellipse 260px 300px at 700px 380px, rgba(80,140,200,.55), rgba(80,140,200,0) 72%),
      linear-gradient(180deg, #ffffff 0%, #f1f4f8 30%, #dfe6ee 65%, #cfd9e4 100%);
  }
  .course-title {
    position: absolute; left: 0; top: 58px; width: 900px; text-align: center;
    font-family: "Montserrat", sans-serif; font-weight: 900; font-size: 60px;
    color: var(--navy-ink); letter-spacing: -.5px; line-height: 1;
  }

  .info-card { position: absolute; left: 75px; top: 171px; width: 382px; height: 362px; }
  .info-card__top {
    position: absolute; left: 0; top: 0; width: 382px; height: 210px;
    background: var(--sky); border-top-right-radius: 90px;
  }
  .info-card__bottom {
    position: absolute; left: 0; top: 210px; width: 382px; height: 152px;
    background: rgba(66,97,143,.96); border-bottom-left-radius: 90px;
  }
  .city {
    position: absolute; top: 20px; width: 100%; text-align: center;
    font-family: "Raleway", sans-serif; font-weight: 700; font-size: 38px; color: var(--white);
  }
  .dotted { position: absolute; left: 50px; width: 282px; border-top: 1.5px dotted rgba(255,255,255,.85); }
  .dotted--a { top: 77px; } .dotted--b { top: 110px; }
  .sessions {
    position: absolute; top: 81px; width: 100%; text-align: center;
    font-family: "Raleway", sans-serif; font-weight: 700; font-size: 17.5px; color: var(--white);
  }
  .start-date {
    position: absolute; top: 112px; width: 100%; text-align: center;
    font-family: "Raleway", sans-serif; font-weight: 700; font-size: 37px; color: var(--white);
  }
  .scholarships {
    position: absolute; top: 166px; width: 100%; text-align: center;
    font-family: "Raleway", sans-serif; font-weight: 300; font-size: 18.5px; color: var(--white);
  }
  .early-bird {
    position: absolute; top: 28px; width: 100%; text-align: center;
    font-family: "Lato", sans-serif; font-weight: 700; font-size: 21px; color: var(--white);
  }
  .early-bird-note {
    position: absolute; top: 64px; width: 100%; text-align: center;
    font-family: "Lato", sans-serif; font-weight: 400; font-size: 18px; line-height: 22px; color: var(--white);
  }

  .headline-band {
    position: absolute; left: 0; top: 555px; width: 900px; height: 114px;
    background: var(--navy); text-align: center; color: var(--white);
    font-family: "Montserrat", sans-serif;
  }
  .headline-band__title { position: absolute; top: 19px; width: 100%; font-weight: 800; font-size: 29px; letter-spacing: .5px; }
  .headline-band__tagline { position: absolute; top: 62px; width: 100%; font-weight: 400; font-size: 24px; letter-spacing: .3px; }

  .topics-heading {
    position: absolute; top: 698px; width: 900px; text-align: center;
    font-family: "Montserrat", sans-serif; font-size: 31px; color: var(--navy-ink); letter-spacing: -.5px;
  }
  .topics-heading strong { font-weight: 800; }
  .topics-heading span { font-weight: 300; }

  .topic { position: absolute; width: 170px; text-align: center; }
  .topic svg { display: block; margin: 0 auto; width: 82px; height: 82px; }
  .topic__label {
    margin-top: 16px; font-family: "Red Hat Display", sans-serif; font-weight: 700;
    font-size: 15.5px; line-height: 18px; color: var(--navy-ink);
  }
  .icon-ring { fill: none; stroke: var(--ring-ink); stroke-width: 1.3; }
  .icon-line { fill: none; stroke: var(--icon-ink); stroke-width: 1.8; stroke-linecap: round; stroke-linejoin: round; }

  .footer-rule { position: absolute; left: 0; top: 1077px; width: 900px; border-top: 1.5px dotted var(--rule); }
</style>
</head>
<body>
<div class="ad">
  <div class="hero-scene" role="img" aria-label="Hillside vineyard rows under a soft blue sky"></div>
  <h1 class="course-title">VINEYARD COURSE</h1>

  <section class="info-card">
    <div class="info-card__top">
      <p class="city">Elmridge</p>
      <div class="dotted dotted--a"></div>
      <p class="sessions">10 -Tuesday evenings sessions</p>
      <div class="dotted dotted--b"></div>
      <p class="start-date">Starting Feb.28</p>
      <p class="scholarships">Limited Partial Scholarships</p>
    </div>
    <div class="info-card__bottom">
      <p class="early-bird">Early Bird Special</p>
      <p class="early-bird-note">For those that started or would<br>like to go into winegrowing</p>
    </div>
  </section>

  <section class="headline-band">
    <h2 class="headline-band__title">MASTERING MODERN VINEYARD MANAGEMENT</h2>
    <p class="headline-band__tagline">INVESTING IN KNOWLEDGE IS INVESTING IN OPPORTUNITIES.</p>
  </section>

  <h3 class="topics-heading"><strong>TOPICS:</strong> <span>PARTIAL LISTING</span></h3>

  <!-- Row one -->
  <div class="topic" style="left:67px; top:760px;">
    <svg viewBox="0 0 82 82"><circle class="icon-ring" cx="41" cy="41" r="40"/>
      <path class="icon-line" d="M18 50h6v12h-6z M24 52c6-3 10-3 16 0h8c3 0 3 4 0 4h-10 M24 60c8 2 14 2 22-2l10-7c3-2 1-5-2-4l-9 5"/>
      <circle class="icon-line" cx="42" cy="36" r="9"/><path class="icon-line" d="M42 31v5l3 2 M38 24l4 3 4-3"/></svg>
    <p class="topic__label">Vineyard<br>investment strategies</p>
  </div>
  <div class="topic" style="left:216px; top:760px;">
    <svg viewBox="0 0 82 82"><circle class="icon-ring" cx="41" cy="41" r="40"/>
      <circle class="icon-line" cx="32" cy="36" r="10"/><circle class="icon-line" cx="32" cy="36" r="4"/>
      <circle class="icon-line" cx="44" cy="42" r="8"/><path class="icon-line" d="M50 48l9 9"/></svg>
    <p class="topic__label">Site assessment</p>
  </div>
  <div class="topic" style="left:365px; top:760px;">
    <svg viewBox="0 0 82 82"><circle class="icon-ring" cx="41" cy="41" r="40"/>
      <path class="icon-line" d="M30 26h10l-3 6c8 4 10 14 6 20H26c-5-6-2-16 6-20z"/>
      <ellipse class="icon-line" cx="54" cy="36" rx="8" ry="3"/><path class="icon-line" d="M46 36v14c0 2 16 2 16 0V36 M46 43c0 2 16 2 16 0"/>
      <circle class="icon-line" cx="42" cy="54" r="7"/></svg>
    <p class="topic__label">Financing</p>
  </div>
  <div class="topic" style="left:514px; top:760px;">
    <svg viewBox="0 0 82 82"><circle class="icon-ring" cx="41" cy="41" r="40"/>
      <rect class="icon-line" x="27" y="20" width="28" height="40" rx="2"/><circle class="icon-line" cx="41" cy="30" r="4"/>
      <path class="icon-line" d="M32 42h18 M32 47h18 M32 52h12"/></svg>
    <p class="topic__label">Yield forecasting</p>
  </div>
  <div class="topic" style="left:663px; top:760px;">
    <svg viewBox="0 0 82 82"><circle class="icon-ring" cx="41" cy="41" r="40"/>
      <path class="icon-line" d="M20 46h5v12h-5z M25 48c6-2 10-2 14 1h7 M25 56c8 2 14 0 20-4l11-8"/>
      <path class="icon-line" d="M30 36v-10l6-4 6 4v10z M46 36V22h8v14"/></svg>
    <p class="topic__label">Estate<br>management</p>
  </div>

  <!-- Row two -->
  <div class="topic" style="left:67px; top:920px;">
    <svg viewBox="0 0 82 82"><circle class="icon-ring" cx="41" cy="41" r="40"/>
      <rect class="icon-line" x="24" y="20" width="28" height="40" rx="2"/>
      <path class="icon-line" d="M29 28h18 M29 34h18 M29 40h18 M29 46h18 M29 52h12 M56 36l4 22"/></svg>
    <p class="topic__label">Vineyard<br>Legal basics</p>
  </div>
  <div class="topic" style="left:216px; top:920px;">
    <svg viewBox="0 0 82 82"><circle class="icon-ring" cx="41" cy="41" r="40"/>
      <rect class="icon-line" x="20" y="20" width="26" height="36" rx="2"/>
      <path class="icon-line" d="M25 30h14 M25 36h14 M25 42h8"/><circle class="icon-line" cx="50" cy="48" r="11"/>
      <path class="icon-line" d="M43 48l4-3 5 3 5-3"/></svg>
    <p class="topic__label">Sourcing land</p>
  </div>
  <div class="topic" style="left:365px; top:920px;">
    <svg viewBox="0 0 82 82"><circle class="icon-ring" cx="41" cy="41" r="40"/>
      <rect class="icon-line" x="36" y="34" width="10" height="14" rx="1"/>
      <path class="icon-line" d="M41 28v-8 M41 54v8 M30 41h-8 M52 41h8 M33 33l-5-5 M49 33l5-5 M33 49l-5 5 M49 49l5 5"/></svg>
    <p class="topic__label">Canopy care</p>
  </div>
  <div class="topic" style="left:514px; top:920px;">
    <svg viewBox="0 0 82 82"><circle class="icon-ring" cx="41" cy="41" r="40"/>
      <circle class="icon-line" cx="33" cy="28" r="3"/><circle class="icon-line" cx="41" cy="26" r="3"/><circle class="icon-line" cx="49" cy="28" r="3"/>
      <path class="icon-line" d="M22 44l8-6 8 4 8-4 14 6 M28 50l8 6 6-2 12-8"/></svg>
    <p class="topic__label">Dealing<br>with wineries</p>
  </div>
  <div class="topic" style="left:663px; top:920px;">
    <svg viewBox="0 0 82 82"><circle class="icon-ring" cx="41" cy="41" r="40"/>
      <circle class="icon-line" cx="50" cy="32" r="10"/><path class="icon-line" d="M46 36l8-8"/>
      <ellipse class="icon-line" cx="32" cy="46" rx="8" ry="3"/><path class="icon-line" d="M24 46v12c0 2 16 2 16 0V46 M24 52c0 2 16 2 16 0"/></svg>
    <p class="topic__label">Tax fundamentals</p>
  </div>

  <div class="footer-rule"></div>
</div>
</body>
</html>
```